Quillmere Supply Chain and Logistic Consulting

Please review the attached Business Card. I want as close to this card with the colors, fonts, and quality of the card as possible. The attached compass should replace the deer head on both sides of the card and the text should say:

Backside
Compass JPEG
Quillmere Logistics
A Supply Chain and Logistics Consulting Company

Frontside
Quillmere Logistics
Ray Falkner - Brookhaven Ridge
President
____________________________________
(555) 314-9027
QuillmereSCL@Examplemail.com
_____________________________________

Bottom Front Side

Target Market(s)

Businesses

Contact Information for Business Card

Backside
Compass JPEG
Quillmere Logistics

Frontside
Quillmere Logistics
President
(555) 314-9027
QuillmereSCL@Examplemail.com

Bottom Front Side

Font styles to use
Serif
Script

Colors

Designer to choose colors to be used in the design.

Requirements
Must have
• See attached card for reference
Nice to have
Should not have

```html
<!DOCTYPE html>
<html lang="en">
<head>
<meta charset="utf-8">
<title>Quillmere Logistics — Business Card</title>
<link rel="stylesheet" href="https://fonts.googleapis.com/css2?family=Cormorant+Garamond:wght@500&family=Tinos:wght@400;700&display=swap">
<style>
  :root {
    --backdrop: #141414;
    --card-top: #0b1535;
    --card-bottom: #040a1d;
    --silver: #dfe3f2;
    --muted-blue: #7d88b8;
    --title-blue: #8f97e0;
    --rule: rgba(190, 200, 235, 0.45);
    --mark-ring: #c9cfe6;
  }
  * { box-sizing: border-box; margin: 0; padding: 0; }
  html, body {
    width: 1200px;
    height: 900px;
    overflow: hidden;
    background: var(--backdrop);
  }
  .canvas {
    width: 1200px;
    height: 900px;
    display: flex;
    flex-direction: column;
    align-items: center;
    justify-content: center;
    gap: 60px;
  }
  .card {
    position: relative;
    width: 665px;
    height: 380px;
    background: linear-gradient(160deg, var(--card-top), var(--card-bottom));
    box-shadow: 0 14px 30px rgba(0, 0, 0, 0.6);
    overflow: hidden;
  }

  /* Back side */
  .card-back {
    display: flex;
    flex-direction: column;
    align-items: center;
  }
  .brand-mark {
    margin-top: 62px;
    width: 104px;
    height: 104px;
    border-radius: 50%;
    border: 2px solid var(--mark-ring);
  }
  .brand-name {
    font-family: "Cormorant Garamond", serif;
    font-weight: 500;
    color: var(--silver);
    letter-spacing: 0.06em;
    text-transform: uppercase;
    white-space: nowrap;
  }
  .card-back .brand-name {
    margin-top: 44px;
    font-size: 30px;
  }
  .tagline {
    font-family: "Cormorant Garamond", serif;
    font-weight: 500;
    font-size: 16px;
    letter-spacing: 0.04em;
    color: var(--muted-blue);
    text-transform: uppercase;
    white-space: nowrap;
  }
  .card-back .tagline {
    position: absolute;
    bottom: 36px;
  }

  /* Front side */
  .front-content {
    position: absolute;
    left: 58px;
    top: 44px;
    width: 470px;
    text-align: center;
  }
  .card-front .brand-name {
    font-size: 38px;
    text-align: left;
  }
  .person-line {
    margin-top: 8px;
    font-family: "Tinos", serif;
    font-size: 24px;
    color: #ffffff;
  }
  .person-title {
    font-family: "Tinos", serif;
    font-weight: 700;
    font-size: 17px;
    color: var(--title-blue);
  }
  .rule {
    height: 1px;
    margin: 18px auto;
    width: 380px;
    background: linear-gradient(90deg, transparent, var(--rule), transparent);
  }
  .contact {
    font-family: "Tinos", serif;
    font-size: 21px;
    line-height: 1.3;
    color: #ffffff;
  }
  .card-front .tagline {
    position: absolute;
    bottom: 30px;
    left: 0;
    right: 0;
    text-align: center;
  }
</style>
</head>
<body>
<main class="canvas">

  <section class="card card-back" aria-label="Business card, back side">
    <div class="brand-mark"></div>
    <h1 class="brand-name">Quillmere Logistics</h1>
    <p class="tagline">A Supply Chain and Logistics Consulting Company</p>
  </section>

  <section class="card card-front" aria-label="Business card, front side">
    <div class="front-content">
      <h2 class="brand-name">Quillmere Logistics</h2>
      <p class="person-line">Ray Falkner - Brookhaven Ridge</p>
      <p class="person-title">President</p>
      <div class="rule"></div>
      <p class="contact">(555) 314-9027<br>QuillmereSCL@Examplemail.com</p>
      <div class="rule"></div>
    </div>
    <p class="tagline">A Supply Chain and Logistics Consulting Company</p>
  </section>

</main>
</body>
</html>
```